Valdane Companies Business Card Design

We need a new business card for our Private Equity Real Estate Development firm, “Valdane” and our EB-5 regional center “Thornmere Regional Center” on one card. We prefer a design that is simple, elegant, and represents the luxury products we design and build as well as the financial security and stability our successful history has produced. We are an industry leader in our field and 3rd generation family business that has evolved into an institutional quality investment platform. Considered design size is standard business card dimensions (3.5 x 2 inches with an additional 1/8 inch space for design elements or backgrounds that extend beyond the finished size of your piece.

Target Market(s)

• High net worth individuals
• Highly skilled technical workers and physicians in the US seeking investment-based immigration opportunities
• Sophisticated private equity investors
• Intermediary partners include domestic attorneys and investment brokers, as well as international agent networks
• US real estate developers

Industry/Entity Type

Finance

Contact Information for Business Card

(Providing placeholder info for personal information, please design for longer character spaces, longer names and addresses etc..)
• Logo for Valdane
• Logo for Thornmere Regional Center
• Full name: Marcus Valdane
• Job title: CEO
• Email address: mvaldane@valdanecompanies.com
• Cell phone number: +1.555.314.2287
• Office number +1.555.628.4410
• Office address: Larkfield Court 5, 4817 Vista Orilla, San Ramon, CA.
• Website: www.valdanecompanies.com

Font styles to use
Serif
Sans Serif

Colors
ec1f27
ffffff
000000

Requirements
Must have
• • Logo for Valdane
• • Logo for Thornmere Regional Center
• - Use rounded corners
• (See .ai file included for logos)
Nice to have
• • Simple, elegant design
• • Aesthetically compatible with our website design (www.valdanecompanies.com)
• • Color palette including but not limited to white, black, and red (as per logos)
Should not have
• - Not too much red color
• - Do not stack both logos on top of each other

```html
<!DOCTYPE html>
<html lang="en">
<head>
<meta charset="utf-8">
<title>Valdane Companies Business Card</title>
<link rel="stylesheet" href="https://fonts.googleapis.com/css2?family=Crimson+Pro:wght@700&family=Open+Sans:wght@400;600&display=swap">
<style>
  :root {
    --red: #b3142a;
    --ink: #333333;
    --paper: #ffffff;
    --night: #0b0b0b;
    --night-text: #2e2e2e;
    --frame: #d6d6d6;
    --stage: #e9e9e9;
    --serif: "Crimson Pro", Georgia, serif;
    --sans: "Open Sans", Arial, sans-serif;
  }
  * { box-sizing: border-box; margin: 0; padding: 0; }
  html, body { width: 1200px; height: 900px; overflow: hidden; }
  body {
    background: var(--stage);
    display: flex; flex-direction: column; align-items: center; justify-content: center;
    gap: 50px;
  }
  .card {
    position: relative;
    width: 630px; height: 360px;
    border-radius: 26px;
    overflow: hidden;
    box-shadow: 0 6px 20px rgba(0,0,0,.18);
  }
  .card-front { background: var(--paper); }
  .card-back { background: var(--night); display: flex; align-items: center; justify-content: center; }

  .front-frame { position: absolute; left: 0; top: 0; }

  .center-brand {
    position: absolute; top: 52px; left: 0; right: 0;
    display: flex; align-items: center; justify-content: center; gap: 12px;
  }
  .brand-square { width: 26px; height: 26px; background: var(--red); }
  .center-name {
    font-family: var(--serif); font-weight: 700; font-size: 26px;
    color: var(--red); letter-spacing: .5px;
  }

  .person { position: absolute; top: 104px; left: 0; right: 0; text-align: center; }
  .person-name {
    font-family: var(--serif); font-weight: 700; font-size: 36px; color: var(--red); line-height: 1;
  }
  .person-title {
    margin-top: 8px;
    font-family: var(--sans); font-size: 15px; letter-spacing: 9px; color: var(--ink); padding-left: 9px;
  }

  .contact {
    position: absolute; top: 200px;
    font-family: var(--sans); font-size: 14px; color: var(--ink);
    display: flex; flex-direction: column; gap: 8px;
  }
  .contact-phones { left: 58px; }
  .contact-online { left: 318px; }
  .contact-row { display: flex; align-items: center; gap: 8px; white-space: nowrap; }
  .contact-label { display: inline-block; width: 44px; }
  .icon { width: 16px; height: 16px; flex: none; }
  .icon-gap { width: 16px; flex: none; }

  .address {
    position: absolute; bottom: 26px; left: 0; right: 0; text-align: center;
    font-family: var(--sans); font-size: 15px; color: var(--red);
  }

  .back-brand { display: flex; align-items: center; gap: 18px; }
  .back-square { width: 44px; height: 44px; background: var(--night-text); }
  .back-name {
    font-family: var(--serif); font-weight: 700; font-size: 58px;
    color: var(--night-text); letter-spacing: 3px; text-transform: uppercase;
  }
</style>
</head>
<body>

<section class="card card-front">
  <svg class="front-frame" width="630" height="360" viewBox="0 0 630 360" aria-hidden="true">
    <path d="M52 30 H578 L590 42 V278 L578 290 H52 L40 278 V42 Z" fill="none" stroke="var(--frame)" stroke-width="2"/>
  </svg>

  <div class="center-brand">
    <span class="brand-square"></span>
    <span class="center-name">Thornmere Regional Center</span>
  </div>

  <div class="person">
    <div class="person-name">Marcus Valdane</div>
    <div class="person-title">CEO</div>
  </div>

  <div class="contact contact-phones">
    <div class="contact-row">
      <svg class="icon" viewBox="0 0 16 16" aria-hidden="true"><circle cx="8" cy="8" r="8" fill="var(--red)"/><path d="M5.5 4.5 L7 6 L6.2 7 Q7 8.8 9 9.8 L10 9 L11.5 10.5 L10.5 11.5 Q6.5 11 4.5 5.5 Z" fill="#fff"/></svg>
      <span><span class="contact-label">Office</span>: +1.555.628.4410</span>
    </div>
    <div class="contact-row">
      <span class="icon-gap"></span>
      <span><span class="contact-label">Cell</span>: +1.555.314.2287</span>
    </div>
  </div>

  <div class="contact contact-online">
    <div class="contact-row">
      <svg class="icon" viewBox="0 0 16 16" aria-hidden="true"><circle cx="8" cy="8" r="8" fill="var(--red)"/><rect x="4" y="5" width="8" height="6" fill="none" stroke="#fff" stroke-width="1.2"/><path d="M4 5 L8 8.5 L12 5" fill="none" stroke="#fff" stroke-width="1.2"/></svg>
      <span>mvaldane@valdanecompanies.com</span>
    </div>
    <div class="contact-row">
      <svg class="icon" viewBox="0 0 16 16" aria-hidden="true"><circle cx="8" cy="8" r="8" fill="var(--red)"/><circle cx="8" cy="8" r="4.2" fill="none" stroke="#fff" stroke-width="1.1"/><path d="M3.8 8 H12.2 M8 3.8 Q5.8 8 8 12.2 M8 3.8 Q10.2 8 8 12.2" fill="none" stroke="#fff" stroke-width="1"/></svg>
      <span>www.valdanecompanies.com</span>
    </div>
  </div>

  <p class="address">Larkfield Court 5, 4817 Vista Orilla, San Ramon, CA.</p>
</section>

<section class="card card-back">
  <div class="back-brand">
    <span class="back-square"></span>
    <span class="back-name">Valdane</span>
  </div>
</section>

</body>
</html>
```